We are a recruitment company based in Norwich/Cambridge England.
I have included our company logo which we want to remain the same.

What we are looking for is a new creative Business card which will really stand out!!

Contact Information for Business Card

Harriet Dunmore
email: Harriet@plavex.co.uk
Address: Brackwell House
Fenmoor Enterprise Park
Partridge Way
Norwich
QB9 3KX
Tel:01632 960418

```html
<!DOCTYPE html>
<html lang="en">
<head>
<meta charset="utf-8">
<title>Plavex Business Card</title>
<link rel="stylesheet" href="https://fonts.googleapis.com/css2?family=Montserrat:wght@500;600;700&family=Open+Sans:wght@400;600&display=swap">
<style>
  :root {
    --backdrop: #4b433d;
    --card: #0d0d0d;
    --card-edge: #1c1c1c;
    --green: #8cc63f;
    --grey: #8e8c93;
    --silver: #e6e6e6;
    --text: #eeeeee;
    --muted: #bdbdbd;
    --rule: #5a5a5a;
  }
  * { box-sizing: border-box; margin: 0; padding: 0; }
  html, body {
    width: 1200px; height: 900px; overflow: hidden;
    background: var(--backdrop);
  }
  .canvas {
    position: relative; width: 1200px; height: 900px;
    display: flex; align-items: center; justify-content: center; gap: 60px;
  }
  .card {
    position: relative; width: 525px; height: 300px;
    background: var(--card);
    border: 1px solid var(--card-edge);
    box-shadow: 0 18px 40px rgba(0,0,0,.45);
    color: var(--text);
    font-family: "Open Sans", sans-serif;
  }

  /* Contact side */
  .card-front .brand-block {
    position: absolute; left: 40px; top: 0; bottom: 0; width: 220px;
    display: flex; align-items: center; gap: 14px;
  }
  .brand-dot {
    width: 54px; height: 54px; border-radius: 50%;
    background: var(--green); flex: none;
  }
  .brand-name-front {
    font-family: "Montserrat", sans-serif; font-weight: 600;
    font-size: 36px; color: var(--grey); letter-spacing: .5px;
  }
  .divider {
    position: absolute; left: 285px; top: 40px; bottom: 40px;
    width: 1px; background: var(--rule);
  }
  .contact {
    position: absolute; left: 303px; top: 42px; right: 12px;
  }
  .person-name {
    font-family: "Montserrat", sans-serif; font-weight: 700;
    font-size: 18px; letter-spacing: .2px; text-transform: uppercase;
    line-height: 1.1; white-space: nowrap;
  }
  .person-name .first { color: var(--green); }
  .person-name .last { color: var(--grey); }
  .person-role { font-size: 12.5px; color: var(--muted); margin-bottom: 12px; }
  .contact-list { list-style: none; }
  .contact-list li {
    display: flex; align-items: center; gap: 9px;
    font-size: 13px; line-height: 19px; color: var(--text);
    white-space: nowrap;
  }
  .contact-list svg { width: 11px; height: 11px; flex: none; fill: var(--green); }
  .address { font-size: 13px; line-height: 18px; margin-top: 8px; color: var(--text); }

  /* Brand side */
  .card-back {
    display: flex; align-items: center; justify-content: center;
  }
  .brand-lockup { display: flex; align-items: center; gap: 18px; }
  .brand-dot-back {
    width: 72px; height: 72px; border-radius: 50%; background: var(--silver);
  }
  .brand-text { display: flex; flex-direction: column; }
  .brand-name-back {
    font-family: "Montserrat", sans-serif; font-weight: 600;
    font-size: 52px; line-height: 1; color: var(--silver);
  }
  .brand-tagline {
    font-family: "Montserrat", sans-serif; font-weight: 500;
    font-size: 10px; letter-spacing: 3px; color: var(--silver);
    margin-top: 6px; text-align: right;
  }
</style>
</head>
<body>
<main class="canvas">

  <section class="card card-front" aria-label="Business card, contact side">
    <div class="brand-block">
      <span class="brand-dot" aria-hidden="true"></span>
      <span class="brand-name-front">Plavex</span>
    </div>
    <div class="divider"></div>
    <div class="contact">
      <h1 class="person-name"><span class="first">Harriet</span> <span class="last">Dunmore</span></h1>
      <p class="person-role">Managing Director</p>
      <ul class="contact-list">
        <li>
          <svg viewBox="0 0 12 12" aria-hidden="true"><path d="M1 4c0-2 2-3 5-3s5 1 5 3l-2 1-1-2H4L3 5zM3 6h6l1 5H2z"/></svg>
          01632 960418
        </li>
        <li>
          <svg viewBox="0 0 12 12" aria-hidden="true"><path d="M0 2h12v8H0zM1 3l5 4 5-4z" fill-rule="evenodd"/></svg>
          Harriet@plavex.co.uk
        </li>
        <li>
          <svg viewBox="0 0 12 12" aria-hidden="true"><circle cx="6" cy="6" r="5.5"/></svg>
          www.plavex.co.uk
        </li>
      </ul>
      <p class="address">Brackwell House,<br>Fenmoor Enterprise Park,<br>Partridge Way,<br>Norwich QB9 3KX</p>
    </div>
  </section>

  <section class="card card-back" aria-label="Business card, brand side">
    <div class="brand-lockup">
      <span class="brand-dot-back" aria-hidden="true"></span>
      <div class="brand-text">
        <span class="brand-name-back">Plavex</span>
        <span class="brand-tagline">Technology Recruitment</span>
      </div>
    </div>
  </section>

</main>
</body>
</html>
```